Telecommunications/Power civil contractor needs business card design

Were a new telecommunications/power underground civil contractor that is looking for a new business card design. Our company colours are silver or grey and orange. Feel free to use the white background logo or the black background logo.

Target Market(s)

Local contractors, utility companies, private sector mining/energy companies, developers.

Industry/Entity Type

Telecommunications

Contact Information for Business Card

Each card will need the following info:
Persons name:
Title:
E-mail:
Phone number:
Shop Address:
Mailing Address:

Requirements
Must have
• Each card will need the following info:
• Persons name:
• Title:
• E-mail:
• Phone number:
• Shop Address:
• Mailing Address:

```html
<!DOCTYPE html>
<html lang="en">
<head>
<meta charset="utf-8">
<title>Northline Civil Works – Business Card</title>
<link rel="stylesheet" href="https://fonts.googleapis.com/css2?family=Open+Sans:wght@400;600;800&display=swap">
<style>
  :root {
    --page-bg: #d9d4cc;
    --card-light: #ebe9e6;
    --card-light-edge: #dcd9d5;
    --brand-red: #e23a1e;
    --brand-red-deep: #c92a12;
    --brand-red-soft: #ee5a3a;
    --ink-white: #ffffff;
    --ink-white-soft: rgba(255,255,255,0.88);
    --logo-grey: #3a3a3a;
    --logo-ring: #d8321a;
  }
  html, body {
    margin: 0;
    padding: 0;
    width: 1200px;
    height: 969px;
    overflow: hidden;
    background: var(--page-bg);
    font-family: "Open Sans", Arial, sans-serif;
  }
  .canvas {
    position: relative;
    width: 1200px;
    height: 969px;
  }
  .business-card {
    position: absolute;
    left: 100px;
    top: 200px;
    width: 1000px;
    height: 570px;
    display: flex;
    background: linear-gradient(135deg, var(--card-light) 0%, var(--card-light-edge) 100%);
    box-shadow: 0 18px 40px rgba(0,0,0,0.18);
  }
  .contact-panel {
    position: relative;
    width: 472px;
    height: 100%;
    background: linear-gradient(160deg, var(--brand-red-soft) 0%, var(--brand-red) 45%, var(--brand-red-deep) 100%);
    color: var(--ink-white);
  }
  .person-name {
    position: absolute;
    left: 66px;
    top: 68px;
    margin: 0;
    font-size: 31px;
    font-weight: 600;
    letter-spacing: 0.5px;
  }
  .person-title {
    position: absolute;
    left: 66px;
    top: 110px;
    margin: 0;
    font-size: 24px;
    font-weight: 400;
    color: var(--ink-white-soft);
  }
  .address {
    position: absolute;
    left: 66px;
    margin: 0;
    font-style: normal;
    font-size: 22px;
    line-height: 32px;
    color: var(--ink-white-soft);
  }
  .shop-address { top: 226px; }
  .mailing-address { top: 304px; }
  .contact-list {
    position: absolute;
    left: 66px;
    top: 392px;
    margin: 0;
    padding: 0;
    list-style: none;
    font-size: 22px;
    line-height: 38px;
    color: var(--ink-white-soft);
  }
  .contact-list li {
    display: flex;
    align-items: center;
    gap: 14px;
  }
  .contact-icon {
    width: 20px;
    height: 20px;
    flex: none;
  }
  .brand-panel {
    position: relative;
    flex: 1;
    height: 100%;
  }
  .brand-mark {
    position: absolute;
    left: 195px;
    top: 245px;
    width: 150px;
    height: 150px;
    border: 12px solid var(--logo-ring);
    border-radius: 50%;
    box-sizing: border-box;
  }
  .brand-name {
    position: absolute;
    left: 0;
    right: 0;
    top: 432px;
    margin: 0;
    text-align: center;
    font-size: 30px;
    line-height: 36px;
    font-weight: 800;
    letter-spacing: 1px;
    color: var(--logo-grey);
    text-transform: uppercase;
  }
</style>
</head>
<body>
<div class="canvas">
  <section class="business-card">
    <div class="contact-panel">
      <h1 class="person-name">DANIEL REYES</h1>
      <p class="person-title">CEO/Founder</p>
      <address class="address shop-address">Shop: 4120 Willow Creek Rd<br>Fairbanks, Alaska 99701</address>
      <address class="address mailing-address">Mail: PO Box 7321<br>Fairbanks, Alaska 99707</address>
      <ul class="contact-list">
        <li>
          <svg class="contact-icon" viewBox="0 0 20 20" aria-hidden="true"><path fill="#fff" d="M4.5 1.5l3 3.2-1.8 2.3c1 2.2 2.9 4.1 5.2 5.2l2.3-1.8 3.3 3-1.6 3.1C9 16.3 3.6 10.9 1.4 4.1z"/></svg>
          907 555 0148
        </li>
        <li>
          <svg class="contact-icon" viewBox="0 0 20 20" aria-hidden="true"><rect x="1.5" y="4" width="17" height="12" fill="none" stroke="#fff" stroke-width="1.8"/><path d="M2 4.8l8 6 8-6" fill="none" stroke="#fff" stroke-width="1.8"/></svg>
          daniel@northlinecivil.com
        </li>
        <li>
          <svg class="contact-icon" viewBox="0 0 20 20" aria-hidden="true"><circle cx="10" cy="10" r="8" fill="none" stroke="#fff" stroke-width="1.8"/><ellipse cx="10" cy="10" rx="3.4" ry="8" fill="none" stroke="#fff" stroke-width="1.5"/><path d="M2 10h16" stroke="#fff" stroke-width="1.5"/></svg>
          www.northlinecivil.com
        </li>
      </ul>
    </div>
    <div class="brand-panel">
      <div class="brand-mark"></div>
      <p class="brand-name">Northline Civil<br>Works Inc</p>
    </div>
  </section>
</div>
</body>
</html>
```